New Website Design for PHOVAN.org

We are looking for a new website design for PHOVAN.org. PHOVAN is a non profit home inspector association based in California. Home Inspectors are people that come out and look at a house before it's purchased to let the buyer know of any defects that may exist.
Our site is based on Joomla so if you'll be able to make a Joomla 3 template as well, please let us know (not required, but a bonus).
We would like to see designs that incorporate royal blue, white and chrome into the site as that's our main business colors.
We would like a place for rotating banners though they don't need to be the same size as the current site.
We would like navigation to be easier to manage with menus only across the top (via drop down menus) where we are going to sort out the items currently on the side. Possibly the front page could have a graphic link to separate portals for Realtors, Home Buyers and Inspectors, but that's just one option.
We would like a good mobile design or something that will scale easily to mobile.
The Find an Inspector feature is important and should stand out. The ASK PHOVANr site
Current home page feels a bit busy. Would like to simplify a bit.

```html
<!DOCTYPE html>
<html lang="en">
<head>
<meta charset="utf-8">
<title>PHOVAN Home Inspection Association</title>
<link href="https://fonts.googleapis.com/css2?family=Open+Sans:wght@400;600&family=Roboto:ital,wght@0,400;0,500;0,700;1,400;1,500&family=Source+Sans+3:wght@400;600&display=swap" rel="stylesheet">
<style>
:root{
  --royal:#2d4397;
  --royal-dark:#1f2f75;
  --text:#444;
  --muted:#8a8a8a;
  --line:#cfcfcf;
  --card:#ececec;
  --footer:#3a3a3a;
  --footer-bar:#1e1e1e;
  --white:#fff;
}
*{margin:0;padding:0;box-sizing:border-box}
html,body{width:867px;height:1200px;overflow:hidden;background:var(--white)}
body{position:relative;font-family:"Open Sans",sans-serif;color:var(--text)}
.abs{position:absolute}
/* header */
.brand{left:86px;top:0;width:196px;height:86px;background:var(--white);box-shadow:0 1px 4px rgba(0,0,0,.25);z-index:3;display:flex;align-items:center;gap:10px;padding-left:14px}
.brand-mark{width:30px;height:30px;border-radius:50%;background:var(--royal)}
.brand-name{font-family:"Roboto",sans-serif;font-weight:500;font-size:20px;color:var(--royal);letter-spacing:.5px}
.main-nav{left:325px;top:7px;display:flex;align-items:center;gap:21px;font-family:"Roboto",sans-serif;font-size:10.5px;color:#888}
.main-nav .active{background:var(--royal);color:var(--white);padding:5px 14px;border-radius:3px;border:1px solid var(--royal-dark);font-weight:500}
.main-nav .find{color:var(--royal);font-weight:700}
.search{width:13px;height:13px}
/* hero */
.hero{left:86px;top:34px;width:694px;height:286px;background:linear-gradient(180deg,#8a6a52 0%,#b49a80 45%,#c6a67a 75%,#b08e5a 100%)}
.hero-caption{left:106px;top:154px;width:294px;height:100px;background:rgba(70,60,55,.72);padding:4px 6px;color:var(--white);font-family:"Source Sans 3",sans-serif}
.hero-caption h1{font-weight:400;font-size:20px;line-height:23px;letter-spacing:-.6px}
.hero-caption h1 span{font-size:23px;font-weight:600}
.hero-caption p{font-size:9px;line-height:13.5px;margin-top:3px;padding-right:4px}
.dots{left:112px;top:295px;display:flex;gap:3px;align-items:center}
.dots i{width:5px;height:5px;border-radius:50%;background:#555;display:block}
.dots i.on{width:7px;height:7px;background:var(--royal)}
/* features */
.feature{top:346px;width:162px}
.feature-head{display:flex;gap:4px;align-items:flex-start}
.feature-head svg{width:24px;height:24px;flex:none}
.feature h2{font-family:"Roboto",sans-serif;font-style:italic;font-weight:500;font-size:16px;color:#555;line-height:16px}
.feature .sub{font-size:8.3px;color:#444;margin-top:1px}
.feature p{font-family:"Roboto",sans-serif;font-size:8.8px;line-height:13px;letter-spacing:.3px;color:var(--muted);margin-top:14px}
.btn{display:inline-block;background:var(--royal);color:var(--white);font-family:"Roboto",sans-serif;font-size:8px;border:1px solid var(--royal-dark);border-radius:3px;padding:5px 8px;margin-top:6px;box-shadow:inset 0 1px 0 rgba(255,255,255,.3)}
.rule{left:86px;width:694px;border-top:1px dotted var(--line)}
/* welcome */
.welcome{left:94px;top:540px;width:492px}
.section-title{font-family:"Roboto",sans-serif;font-style:italic;font-weight:400;font-size:16px;color:#555;line-height:20px}
.welcome p{font-family:"Roboto",sans-serif;font-size:8.7px;line-height:13px;color:var(--muted);margin-top:10px}
.welcome .btn{font-size:9px;padding:7px 8px;margin-top:9px}
.welcome-photo{left:594px;top:589px;width:180px;height:107px;border:1px solid #ddd;padding:5px;background:var(--white)}
.welcome-photo div{width:100%;height:100%;background:linear-gradient(120deg,#3d5f9e 0%,#6f94d0 55%,#c8c4b8 100%)}
/* recent works */
.works-title{left:94px;top:736px}
.arrows{left:740px;top:738px;display:flex;gap:6px}
.card{top:768px;width:157px;height:213px;background:var(--card)}
.card .ph{height:160px}
.card h3{font-family:"Roboto",sans-serif;font-weight:400;font-size:12px;color:#444;margin:16px 0 0 8px}
.card p{font-family:"Roboto",sans-serif;font-size:8.5px;color:#444;margin:3px 0 0 7px}
/* footer */
.footer{left:0;top:1002px;width:867px;height:164px;background:var(--footer);color:#eee}
.fcol{top:22px}
.fcol h4{font-family:"Roboto",sans-serif;font-weight:400;font-size:12px;color:var(--white);margin-bottom:14px}
.fcol p,.fcol li{font-size:8px;line-height:12px;list-style:none}
.fcol li{margin-bottom:4px}
.fcol .who{font-style:italic;font-weight:600;margin:3px 0 12px}
.field{width:134px;height:19px;background:#f2f2f2;border-radius:3px;font-size:7.5px;color:#aaa;padding:5px 6px;margin-bottom:8px}
.forgot{font-size:8px;color:#ccc;margin:2px 0 6px 5px}
.login{display:inline-block;background:var(--white);color:var(--royal);font-family:"Roboto",sans-serif;font-size:8.5px;font-weight:500;padding:3px 12px;border-radius:2px}
.bar{left:0;top:1166px;width:867px;height:34px;background:var(--footer-bar);color:#ddd;font-size:8px}
.bar .copy{position:absolute;left:88px;top:12px}
.bar nav{position:absolute;right:87px;top:12px;display:flex;gap:14px}
</style>
</head>
<body>

<header>
  <div class="abs brand"><span class="brand-mark"></span><span class="brand-name">PHOVAN</span></div>
  <nav class="abs main-nav">
    <span class="active">Home</span><span class="find">Find an Inspector</span><span>Home Buyers &amp; Sellers</span><span>Real Estate Agents</span><span>Inspectors</span>
    <svg class="search" viewBox="0 0 14 14"><circle cx="5.5" cy="5.5" r="4" fill="none" stroke="#2d4397" stroke-width="2"/><path d="M8.5 8.5L13 13" stroke="#2d4397" stroke-width="2.4" stroke-linecap="round"/></svg>
  </nav>
</header>

<section>
  <div class="abs hero" role="img" aria-label="Smiling home inspector holding a clipboard in front of a brick house"></div>
  <div class="abs hero-caption">
    <h1>The Leader in<br><span>Home Inspection Service</span></h1>
    <p>Le Lorem Ipsum est simplement du faux texte employé dans la composition et la mise en page avant impression. Le Lorem Ipsum est le faux.</p>
  </div>
  <div class="abs dots"><i></i><i></i><i class="on"></i><i></i></div>
</section>

<section>
  <div class="abs feature" style="left:94px">
    <div class="feature-head"><svg viewBox="0 0 24 24"><path d="M2 11L11 3l9 8h-3v4H5v-4z" fill="#2d4397"/><rect x="3" y="13" width="14" height="9" fill="none" stroke="#2d4397" stroke-width="1.6"/><path d="M10 15v5M8 16h4v2H8v2h4" stroke="#2d4397" stroke-width="1.2" fill="none"/></svg>
      <div><h2>Home Realtors</h2><div class="sub">Lorem ipsum dolor sit amet.</div></div></div>
    <p>Lorem ipsum dolor sit amet, consectetur adipisicing elit, sed do eiusmod tempor incididunt ut labore et dolore magna aliqua. Ut enim ad minim veniam, quis nostrud exercitation ullamco laboris nisi ut aliquip ex ea commodo consequat.</p>
    <span class="btn">LEARN MORE</span>
  </div>
  <div class="abs feature" style="left:265px">
    <div class="feature-head"><svg viewBox="0 0 24 24"><path d="M2 12L11 3l9 9h-3v3H5v-3z" fill="#2d4397"/><circle cx="10" cy="18" r="3" fill="none" stroke="#2d4397" stroke-width="1.8"/><path d="M13 18h8v2" stroke="#2d4397" stroke-width="1.8" fill="none"/></svg>
      <div><h2>Home Realtors</h2><div class="sub">Lorem ipsum dolor sit amet.</div></div></div>
    <p>Lorem ipsum dolor sit amet, consectetur adipisicing elit, sed do eiusmod tempor incididunt ut labore et dolore magna aliqua. Ut enim ad minim veniam, quis nostrud exercitation ullamco laboris nisi ut aliquip ex ea commodo consequat.</p>
    <span class="btn">LEARN MORE</span>
  </div>
  <div class="abs feature" style="left:437px">
    <div class="feature-head"><svg viewBox="0 0 24 24"><path d="M2 11L11 3l9 8h-3v2H5v-2z" fill="#2d4397"/><rect x="3" y="13" width="10" height="8" fill="none" stroke="#2d4397" stroke-width="1.4"/><circle cx="15" cy="17" r="3.5" fill="#fff" stroke="#2d4397" stroke-width="1.6"/><path d="M17.5 19.5L21 23" stroke="#2d4397" stroke-width="2"/></svg>
      <div><h2>Home Realtors</h2><div class="sub">Lorem ipsum dolor sit amet.</div></div></div>
    <p>Lorem ipsum dolor sit amet, consectetur adipisicing elit, sed do eiusmod tempor incididunt ut labore et dolore magna aliqua. Ut enim ad minim veniam, quis nostrud exercitation ullamco laboris nisi ut aliquip ex ea commodo consequat.</p>
    <span class="btn">LEARN MORE</span>
  </div>
  <div class="abs feature" style="left:608px">
    <div class="feature-head"><svg viewBox="0 0 24 24"><path d="M4 20L18 6M4 6l14 14" stroke="#2d4397" stroke-width="3" stroke-linecap="round"/><circle cx="5" cy="5" r="3" fill="#2d4397"/><circle cx="19" cy="19" r="3" fill="#2d4397"/></svg>
      <div><h2>Home Realtors</h2><div class="sub">Lorem ipsum dolor sit amet.</div></div></div>
    <p>Lorem ipsum dolor sit amet, consectetur adipisicing elit, sed do eiusmod tempor incididunt ut labore et dolore magna aliqua. Ut enim ad minim veniam, quis nostrud exercitation ullamco laboris nisi ut aliquip ex ea commodo consequat.</p>
    <span class="btn">LEARN MORE</span>
  </div>
</section>

<div class="abs rule" style="top:520px"></div>

<section>
  <div class="abs welcome">
    <h2 class="section-title">Welcome To<br>PHOVAN Home Inspection Association</h2>
    <p>"Lorem ipsum dolor sit amet, consectetur adipisicing elit, sed do eiusmod tempor incididunt ut labore et dolore magna aliqua. Ut enim ad minim veniam, quis nostrud exercitation ullamco laboris nisi ut aliquip ex ea commodo consequat. Duis aute irure dolor in reprehenderit in voluptate velit esse cillum dolore eu fugiat nulla pariatur.</p>
    <p>Excepteur sint occaecat cupidatat non proident, sunt in culpa qui officia deserunt mollit anim id est laborum duis aute irure dolor in reprehenderit in voluptate velit esse cillum dolore eu fugiat nulla pariatur.</p>
    <span class="btn">READ MORE</span>
  </div>
  <div class="abs welcome-photo"><div role="img" aria-label="Inspector on a ladder checking a roof edge under blue sky"></div></div>
</section>

<div class="abs rule" style="top:718px"></div>

<section>
  <h2 class="abs section-title works-title">Recent Works</h2>
  <div class="abs arrows"><svg width="9" height="12" viewBox="0 0 9 12"><path d="M7 1L2 6l5 5" stroke="#999" stroke-width="1.6" fill="none"/></svg><svg width="9" height="12" viewBox="0 0 9 12"><path d="M2 1l5 5-5 5" stroke="#999" stroke-width="1.6" fill="none"/></svg></div>
  <div class="abs card" style="left:101px"><div class="ph" role="img" aria-label="Builder in a hard hat reading plans at a house frame" style="background:linear-gradient(160deg,#c7d6e4 0%,#d6b98f 50%,#8a6a48 100%)"></div><h3>Path To Access</h3><p>Lorem ipsum dolor sit amet.</p></div>
  <div class="abs card" style="left:271px"><div class="ph" role="img" aria-label="Open book in front of a bookshelf" style="background:linear-gradient(180deg,#5a2a14 0%,#a0521e 45%,#e2c79a 100%)"></div><h3>Educational Publication</h3><p>Lorem ipsum dolor sit amet.</p></div>
  <div class="abs card" style="left:441px"><div class="ph" role="img" aria-label="Red question mark beside a thinking figure" style="background:radial-gradient(circle at 50% 45%,#e46060 0%,#f3dede 35%,#fff 65%)"></div><h3>Ask PHOVAN</h3><p>Lorem ipsum dolor sit amet.</p></div>
  <div class="abs card" style="left:610px"><div class="ph" role="img" aria-label="Online store banner" style="background:linear-gradient(90deg,#fff 0%,#eef3ea 30%,#e8eaf2 70%,#fbefe4 100%)"></div><h3>Ask PHOVAN</h3><p>Lorem ipsum dolor sit amet.</p></div>
</section>

<footer class="abs footer">
  <div class="abs fcol" style="left:90px">
    <h4>Contact Details</h4>
    <p>418 Larkmoor Avenue, Suite 2<br>Fairhaven, 90418</p>
    <p style="margin-top:12px">Phone No. : 00 555 318-7720</p>
    <p style="margin-top:12px">E-mail : hello@larkmoorhall.net</p>
  </div>
  <div class="abs fcol" style="left:281px">
    <h4>SiteMap</h4>
    <ul><li>Lorem Ipsum is simplement</li><li>Dignissim qui blandit praesent</li><li>Eleend oon congue imperdie</li><li>Claritas process dynamicus</li><li>Laoreet dolore magna aliquam</li></ul>
  </div>
  <div class="abs fcol" style="left:456px">
    <h4>Testimonials</h4>
    <p>Lorem Ipsum est simplement du<br>fauxtexte employé.</p><p class="who">Dorian Pell</p>
    <p>Lorem Ipsum est simplement du<br>fauxtexte employé.</p><p class="who">Anonymous</p>
  </div>
  <div class="abs fcol" style="left:642px">
    <h4>Inspector Login</h4>
    <div class="field">username...</div>
    <div class="field">password</div>
    <p class="forgot">Forgot your password</p>
    <span class="login">Log In</span>
  </div>
</footer>
<div class="abs bar">
  <span class="copy">Copyright 2013. PHOVAN, All Rights Reserved.</span>
  <nav><span>Home</span><span>Find an Inspector</span><span>Ask PHOVAN</span><span>Conferences</span></nav>
</div>

</body>
</html>
```